Business card update

Opening a subsidiary of my company in the USA and need to update my logo.
Updates

Reason: Give more time to a good design.

I made a mistake on my briefing. It's only the business card. Thanks for alerting me on the mistake.

All the best

Teodoro

Target Market(s)

We are an Executive Search company and our target audience are executives in large corporations.

Industry/Entity Type

Business

Requirements
Must have
• Keep the logo. In the US the company is called Delia Brunet Executive Search.

```html
<!DOCTYPE html>
<html lang="en">
<head>
<meta charset="utf-8">
<title>Delia Brunet Executive Search – Business Card</title>
<link rel="stylesheet" href="https://fonts.googleapis.com/css2?family=Josefin+Sans:wght@300;400;600&display=swap">
<style>
  :root {
    --backdrop: #e9eceb;
    --card-white: #ffffff;
    --mint-band: #c6f4e6;
    --mint-strong: #3ccfa8;
    --mint-pale: #a9eedb;
    --navy: #2f3f74;
    --ink: #1f2230;
    --ink-soft: #4a4f5c;
    --phone-red: #d2262b;
  }
  * { margin: 0; padding: 0; box-sizing: border-box; }
  html, body {
    width: 1200px; height: 741px; overflow: hidden;
    background: var(--backdrop);
    font-family: "Josefin Sans", "Helvetica Neue", Arial, sans-serif;
  }
  .canvas {
    width: 1200px; height: 741px;
    display: flex; align-items: center; justify-content: center;
  }
  .card {
    width: 1000px; height: 580px;
    background: var(--card-white);
    display: flex; flex-direction: column;
    box-shadow: 0 6px 24px rgba(0,0,0,0.12);
  }
  .card-header {
    height: 169px;
    display: flex; align-items: center; justify-content: center;
  }
  .brand {
    position: relative;
    padding-top: 22px;
  }
  .brand-rule {
    position: absolute; top: 0; left: 0; right: 0;
    height: 2px; background: var(--mint-pale);
  }
  .brand-name {
    font-size: 40px; font-weight: 400;
    letter-spacing: 8px;
    color: var(--navy);
    white-space: nowrap;
  }
  .contact-band {
    height: 268px;
    background: var(--mint-band);
    display: flex; align-items: center; justify-content: space-between;
    padding: 0 40px 0 55px;
  }
  .person-name {
    font-size: 42px; font-weight: 400;
    color: var(--mint-strong);
    margin-bottom: 16px;
  }
  .phone {
    display: flex; align-items: center; gap: 14px;
    font-size: 33px; color: var(--ink);
  }
  .phone svg { width: 26px; height: 26px; }
  .online-list { list-style: none; }
  .online-list li {
    display: flex; align-items: center; gap: 26px;
    font-size: 24px; font-weight: 300; color: var(--ink-soft);
    margin: 22px 0;
  }
  .online-list svg { width: 32px; height: 32px; }
  .card-footer {
    flex: 1;
    display: flex; flex-direction: column; align-items: center; justify-content: center;
    gap: 10px;
  }
  .company-line {
    display: flex; align-items: center; width: 100%;
    padding: 0 6px; gap: 8px;
  }
  .company-line::before, .company-line::after {
    content: ""; flex: 1; height: 2px; background: var(--mint-pale);
  }
  .company-name {
    font-size: 38px; font-weight: 300;
    letter-spacing: 2px;
    color: var(--mint-pale);
    white-space: nowrap;
  }
  .address {
    font-size: 24px; font-weight: 300;
    color: var(--mint-pale);
  }
</style>
</head>
<body>
<main class="canvas">
  <article class="card">
    <header class="card-header">
      <div class="brand">
        <span class="brand-rule"></span>
        <span class="brand-name">DELIA BRUNET</span>
      </div>
    </header>

    <section class="contact-band">
      <div class="person">
        <h1 class="person-name">Teodoro S. Brunet</h1>
        <p class="phone">
          <svg viewBox="0 0 24 24" aria-hidden="true"><path fill="var(--phone-red)" d="M6.6 10.8c1.4 2.8 3.8 5.1 6.6 6.6l2.2-2.2c.3-.3.7-.4 1-.2 1.1.4 2.3.6 3.6.6.6 0 1 .4 1 1V20c0 .6-.4 1-1 1C10.6 21 3 13.4 3 4c0-.6.4-1 1-1h3.5c.6 0 1 .4 1 1 0 1.3.2 2.5.6 3.6.1.3 0 .7-.2 1z"/></svg>
          305 555-0147
        </p>
      </div>
      <ul class="online-list">
        <li>
          <svg viewBox="0 0 24 24" aria-hidden="true"><rect x="2" y="5" width="20" height="14" rx="2" fill="var(--mint-pale)"/><path d="M3 6l9 7 9-7" fill="none" stroke="var(--mint-band)" stroke-width="1.5"/></svg>
          www.dbexecutivesearch.com
        </li>
        <li>
          <svg viewBox="0 0 24 24" aria-hidden="true"><circle cx="12" cy="12" r="10" fill="var(--mint-pale)"/><path d="M2 12h20M12 2c3 3 3 17 0 20M12 2c-3 3-3 17 0 20" fill="none" stroke="var(--mint-band)" stroke-width="1.3"/></svg>
          tbrunet@dbexecutivesearch.com
        </li>
      </ul>
    </section>

    <footer class="card-footer">
      <div class="company-line"><span class="company-name">Delia Brunet Executive Search</span></div>
      <p class="address">4410 Harbor View Ave Suite 300, Bayside FL 33100</p>
    </footer>
  </article>
</main>
</body>
</html>
```